wealth management firm, professional group, new model

we have a logo that works but we need a card, white background using our colors...clean look

our tag line if can be used in

Guiding Wealth Across Generations

```html
<!DOCTYPE html>
<html lang="en">
<head>
<meta charset="UTF-8">
<title>Halden Wealth Partners – Business Card</title>
<link href="https://fonts.googleapis.com/css2?family=Montserrat:wght@400;500&display=swap" rel="stylesheet">
<style>
  :root {
    --backdrop: #2a2a2a;
    --navy: #162a4c;
    --navy-deep: #13254a;
    --ink: #13264a;
    --paper: #f1f1f1;
    --paper-shade: #e2e2e2;
    --silver: #d9dde4;
  }
  * { margin: 0; padding: 0; box-sizing: border-box; }
  html, body {
    width: 1200px; height: 576px; overflow: hidden;
    background: var(--backdrop);
    font-family: "Montserrat", Arial, sans-serif;
  }
  .stage { position: relative; width: 1200px; height: 576px; }
  .card {
    position: absolute; top: 138px;
    width: 484px; height: 293px;
    border-radius: 10px;
    box-shadow: 0 3px 8px rgba(0,0,0,0.45);
  }
  .card-front {
    left: 102px;
    background: linear-gradient(180deg, var(--navy) 0%, var(--navy-deep) 100%);
  }
  .front-name {
    position: absolute; top: 108px; left: 0; width: 100%;
    text-align: center; color: var(--silver);
    font-size: 30px; font-weight: 400; letter-spacing: 14px;
    padding-left: 14px;
  }
  .front-tagline {
    position: absolute; top: 248px; left: 0; width: 100%;
    text-align: center; color: var(--silver);
    font-size: 13.5px; letter-spacing: 0.6px;
  }
  .card-back {
    left: 596px;
    background: linear-gradient(180deg, var(--paper) 0%, var(--paper-shade) 100%);
    color: var(--ink);
  }
  .person-name {
    position: absolute; top: 38px; left: 26px;
    font-size: 21px; font-weight: 500;
  }
  .person-title {
    position: absolute; top: 66px; left: 26px;
    font-size: 13.5px;
  }
  .contact-list {
    position: absolute; top: 209px; left: 26px; list-style: none;
  }
  .contact-item {
    display: flex; align-items: center; gap: 8px;
    height: 20px; font-size: 12.5px;
  }
  .contact-icon { width: 11px; height: 11px; fill: var(--ink); }
  .contact-icon--web { fill: none; stroke: var(--ink); stroke-width: 1; }
  .brand-block {
    position: absolute; top: 184px; left: 250px; width: 214px;
    text-align: center; font-weight: 400;
  }
  .brand-name {
    font-size: 31px; letter-spacing: 13px; padding-left: 13px; line-height: 1;
  }
  .brand-sub {
    margin-top: 14px; font-size: 13px; letter-spacing: 2px;
  }
  .brand-tagline {
    margin-top: 10px; font-size: 9.5px; letter-spacing: 0.4px; white-space: nowrap;
  }
</style>
</head>
<body>
<main class="stage">
  <section class="card card-front">
    <div class="front-name">HALDEN</div>
    <p class="front-tagline">Guiding Wealth Across Generations</p>
  </section>

  <section class="card card-back">
    <h1 class="person-name">Marcus Halden</h1>
    <p class="person-title">Managing Director</p>

    <ul class="contact-list">
      <li class="contact-item">
        <svg class="contact-icon" viewBox="0 0 12 12" aria-hidden="true"><path d="M1 4 Q6 0 11 4 L10 5.5 L8 4.8 L8 3.8 Q6 3 4 3.8 L4 4.8 L2 5.5 Z M3 6 H9 L10.5 11 H1.5 Z"/></svg>
        <span>555-214-7730</span>
      </li>
      <li class="contact-item">
        <svg class="contact-icon" viewBox="0 0 12 12" aria-hidden="true"><path d="M0.5 2.5 H11.5 V9.5 H0.5 Z M1.5 3.3 L6 6.8 L10.5 3.3 V3 H1.5 Z" fill-rule="evenodd"/></svg>
        <span>marcus@haldenwealth.com</span>
      </li>
      <li class="contact-item">
        <svg class="contact-icon contact-icon--web" viewBox="0 0 12 12" aria-hidden="true"><circle cx="6" cy="6" r="5"/><ellipse cx="6" cy="6" rx="2.2" ry="5"/><line x1="1" y1="6" x2="11" y2="6"/></svg>
        <span>www.haldenwealth.com</span>
      </li>
    </ul>

    <div class="brand-block">
      <div class="brand-name">HALDEN</div>
      <div class="brand-sub">WEALTH PARTNERS</div>
      <div class="brand-tagline">Guiding Wealth Across Generations</div>
    </div>
  </section>
</main>
</body>
</html>
```